High-end construction company needs a business card design

We need a modern looking business card that draws people in, is memorable and looks so good people will want to sick it on their fridges.
On the first side what is needed are:
Logo
My name - Tomasz Brelwik
Title - Managing Director
Website - www.varkelt.co.uk
Email - tomasz@varkelt.co.uk
Telephone - 020 5194 6281
Mobile - 07845139072
On the back side was is needed is a list of all the services we provide:
-Kitchen Renovations
-Bathroom Renovations
-House Renovations
-Garage Conversions
-Extensions
-Loft Conversions
-Conservatories
-Carpentry
-Tiling
-Electrical
-Plumbing & Heating
-Bricklaying
-Landscaping
-Decorating
-Plastering
We would like the colours to be the same shades as on the logo with grey or black for the words.
Target Market(s)
Anyone who needs building work done
Contact Information for Business Card
This business card is for a construction company which strives to deliver excellent service and quality.
The look and feel of the card should represent this.
Requirements
Must have
- On the first side what is needed are:
Logo
My name - Tomasz Brelwik
Title - Managing Director
Website - www.varkelt.co.uk
Email - tomasz@varkelt.co.uk
Telephone - 020 5194 6281
Mobile - 07845139072
Nice to have
- Cool looking features

```html
<!DOCTYPE html>
<html lang="en">
<head>
<meta charset="utf-8">
<title>Varkelt Construction – Business Card</title>
<link href="https://fonts.googleapis.com/css2?family=Roboto:wght@300;400;700;900&display=swap" rel="stylesheet">
<style>
  :root {
    --backdrop: #6e6e6e;
    --green: #73bd42;
    --green-dark: #4a8b3e;
    --white: #ffffff;
    --shadow: #111111;
  }
  * { margin: 0; padding: 0; box-sizing: border-box; }
  html, body {
    width: 1200px; height: 801px; overflow: hidden;
    background: var(--backdrop);
    font-family: "Roboto", Arial, sans-serif;
  }
  .stage { position: relative; width: 1200px; height: 801px; }
  .card {
    position: absolute; top: 274px; width: 443px; height: 263px;
    overflow: hidden;
    box-shadow: 3px 3px 0 var(--shadow);
  }
  .card--front { left: 153px; background: var(--green); }
  .card--back { left: 625px; background: var(--white); }

  .front-artwork {
    position: absolute; left: 200px; top: 0; width: 243px; height: 263px;
    background: linear-gradient(160deg, var(--green) 0%, var(--green-dark) 55%, var(--white) 100%);
    clip-path: polygon(100% 0, 100% 100%, 0 100%, 45% 35%, 45% 12%);
  }
  .owner { position: absolute; left: 26px; top: 71px; color: var(--white); }
  .owner__name { font-weight: 900; font-size: 17px; letter-spacing: 0.2px; text-transform: uppercase; line-height: 20px; }
  .owner__title { font-weight: 400; font-size: 13px; line-height: 16px; }

  .contact { position: absolute; left: 26px; top: 119px; list-style: none; color: var(--white); }
  .contact__item { display: flex; align-items: center; font-size: 13px; line-height: 16px; font-weight: 400; }
  .contact__icon { width: 11px; height: 11px; margin-right: 5px; flex: none; }

  .brand { position: absolute; left: 0; width: 100%; top: 78px; text-align: center; color: var(--green); font-weight: 900; }
  .brand__name { font-size: 46px; line-height: 46px; letter-spacing: 1px; text-transform: uppercase; }
  .brand__sub { font-size: 12px; letter-spacing: 2.6px; text-transform: uppercase; margin-top: 3px; }

  .services { position: absolute; top: 166px; list-style: none; color: var(--green); font-size: 13px; line-height: 15.7px; font-weight: 400; }
  .services li { display: flex; align-items: center; white-space: nowrap; }
  .services li::before {
    content: ""; width: 5px; height: 5px; border-radius: 50%;
    background: var(--green); margin-right: 5px; flex: none;
  }
  .services--one { left: 18px; }
  .services--two { left: 171px; }
  .services--three { left: 292px; top: 164px; }
</style>
</head>
<body>
<main class="stage">
  <section class="card card--front" aria-label="Business card front">
    <div class="front-artwork" role="img" aria-label="Decorative house roof and building illustration"></div>
    <div class="owner">
      <p class="owner__name">Tomasz Brelwik</p>
      <p class="owner__title">Managing Director</p>
    </div>
    <ul class="contact">
      <li class="contact__item">
        <svg class="contact__icon" viewBox="0 0 12 12" aria-hidden="true"><path d="M2.5 1 L4.5 1 L5.2 3.5 L4 4.5 Q5 7 7.5 8 L8.5 6.8 L11 7.5 L11 9.5 Q10.5 11 9 11 Q1 10 1 3 Q1 1.5 2.5 1 Z" fill="none" stroke="#fff" stroke-width="1.2"/></svg>
        020 5194 6281
      </li>
      <li class="contact__item">
        <svg class="contact__icon" viewBox="0 0 12 12" aria-hidden="true"><rect x="3" y="0.8" width="6.5" height="10.4" rx="1" fill="none" stroke="#fff" stroke-width="1.2"/><circle cx="6.25" cy="9.3" r="0.7" fill="#fff"/></svg>
        07845139072
      </li>
      <li class="contact__item">
        <svg class="contact__icon" viewBox="0 0 12 12" aria-hidden="true"><rect x="0.5" y="2.5" width="11" height="7" fill="#fff"/><path d="M0.5 2.5 L6 6.5 L11.5 2.5" fill="none" stroke="#73bd42" stroke-width="1"/></svg>
        tomasz@varkelt.co.uk
      </li>
      <li class="contact__item">
        <svg class="contact__icon" viewBox="0 0 12 12" aria-hidden="true"><g fill="none" stroke="#fff" stroke-width="1"><circle cx="6" cy="6" r="5"/><ellipse cx="6" cy="6" rx="2.2" ry="5"/><path d="M1 6 H11 M1.8 3.5 H10.2 M1.8 8.5 H10.2"/></g></svg>
        www.varkelt.co.uk
      </li>
    </ul>
  </section>

  <section class="card card--back" aria-label="Business card back">
    <div class="brand">
      <p class="brand__name">Varkelt</p>
      <p class="brand__sub">Construction Ltd</p>
    </div>
    <ul class="services services--one">
      <li>Kitchen Renovations</li>
      <li>Bathroom Renovations</li>
      <li>House Renovations</li>
      <li>Garage Conversions</li>
      <li>Extensions</li>
    </ul>
    <ul class="services services--two">
      <li>Loft Conversions</li>
      <li>Conservatories</li>
      <li>Carpentry</li>
      <li>Tiling</li>
      <li>Electrical</li>
    </ul>
    <ul class="services services--three">
      <li>Plumbing &amp; Heating</li>
      <li>Bricklaying</li>
      <li>Landscaping</li>
      <li>Decorating</li>
      <li>Plastering</li>
    </ul>
  </section>
</main>
</body>
</html>
```